Luxury travel agency needs a website design

We are a travel agency specializing in booking luxury vacations. We specialize in Hawaii, Europe and Caribbean, but will do all vacations. I want a very classy website design which would attract luxury clients. The company name is "Harbors and Hammocks Travel Agency". Would love the web design to go with the color scheme of the logo. Hex codes included in files. Logo is attached. Would also love more Grey in the website. I want it very elegant

Coding

Coded - Design and coding required

Font styles to use
Sans Serif
Decorative

Requirements
Must have
• - Consultation Tab or a page where the client can fill out a short form about what vacation that they would want to book. I want this info to be sent to me in order for me to contact them.
- Somewhere with my contact info "email: marla@harborsandhammockstravel.example and phone number"
- Social media links
- About section "Marla Dunbevy - Agency Owner (picture provided)
Marla has been traveling full time for the passed two years and has been very passionate about travel from a young age. Marla is dedicated to working closely with clients to book their dream vacation.
Marla's specializations include honeymoons and anniversaries focusing on travel in Europe, Hawaii and all inclusive resorts in the Caribbean.

```html
<!DOCTYPE html>
<html lang="en">
<head>
<meta charset="utf-8">
<title>Harbors and Hammocks Travel Agency</title>
<link href="https://fonts.googleapis.com/css2?family=Roboto:wght@400;500;700&display=swap" rel="stylesheet">
<style>
:root{
  --orange:#e4603d;
  --orange-dark:#d9502f;
  --gold:#efb64a;
  --ink:#222;
  --grey:#555;
  --grey-light:#f3f3f3;
  --line:#d8d8d8;
  --white:#fff;
}
*{box-sizing:border-box;margin:0;padding:0}
html,body{width:1200px;height:5291px;overflow:hidden}
body{position:relative;font-family:'Roboto',Arial,sans-serif;color:var(--ink);background:var(--white)}
.abs{position:absolute}
section,header,footer{position:absolute;left:0;width:1200px}
/* header */
.site-header{top:0;height:179px}
.search{left:111px;top:37px;width:316px;height:45px;border:1px solid var(--line);border-radius:3px;display:flex;align-items:center}
.search .btn{width:48px;height:45px;background:var(--orange);border-radius:3px 0 0 3px;display:flex;align-items:center;justify-content:center;margin:-1px 0 0 -1px}
.search span{margin-left:18px;font-size:14px;color:#888}
.brand{left:450px;top:40px;width:300px;text-align:center;font-size:22px;font-weight:700;color:var(--ink);letter-spacing:.5px}
.brand small{display:block;font-size:9px;letter-spacing:3px;margin-top:4px}
.call{left:866px;top:37px;display:flex;align-items:center;gap:14px}
.call .ico{width:48px;height:48px;border-radius:50%;background:var(--orange);display:flex;align-items:center;justify-content:center}
.call small{display:block;font-size:12px;color:var(--gold)}
.call strong{font-size:21px;font-weight:500}
.header-rule{left:111px;top:113px;width:978px;height:1px;background:var(--line)}
.nav{left:136px;top:134px;display:flex;font-size:11px;font-weight:700}
.nav a{position:absolute;white-space:nowrap;color:var(--ink);text-decoration:none}
.nav a.active{color:var(--orange)}
.nav a.active:after{content:"";position:absolute;left:-6px;right:-6px;top:26px;height:3px;background:var(--orange)}
.social{left:968px;top:134px;display:flex;gap:18px}
.social i{width:12px;height:12px;border-radius:50%;background:var(--ink);display:block}
/* hero */
.hero{top:179px;height:598px;background:linear-gradient(180deg,#6d9bc4 0%,#a9c6dd 35%,#9aa67a 62%,#5f6a48 85%,#3a4434 100%)}
.welcome{left:493px;top:125px;width:214px;height:45px;background:rgba(206,170,70,.9);color:#fff;font-size:24px;display:flex;align-items:center;justify-content:center}
.hero-title{left:189px;top:187px;width:822px;height:57px;background:rgba(210,80,55,.85);color:#fff;font-size:36px;font-weight:500;display:flex;align-items:center;justify-content:center}
.hero-sub{left:300px;top:270px;width:600px;text-align:center;color:#fff;font-size:15px;line-height:31px}
.booking{left:111px;top:746px;width:976px;height:66px;background:#fff;border-radius:8px;box-shadow:0 6px 18px rgba(0,0,0,.15);overflow:hidden}
.field{position:absolute;top:12px;width:130px}
.field b{display:block;font-size:12px;color:var(--orange);font-weight:500}
.field span{display:block;font-size:11px;margin-top:6px}
.field svg{position:absolute;right:0;top:26px}
.field.sep{border-right:1px solid var(--line);height:40px}
.book-now{position:absolute;right:0;top:0;width:175px;height:66px;background:var(--gold);color:#fff;font-size:15px;font-weight:500;display:flex;align-items:center;justify-content:center}
/* headings */
.h2{font-size:33px;font-weight:500;text-transform:uppercase;color:var(--ink)}
.h2 em{font-style:normal;color:var(--orange)}
.h2.center{position:absolute;left:0;width:1200px;text-align:center}
.bar{position:absolute;height:6px;width:68px;background:var(--gold)}
/* about */
.about{top:812px;height:596px}
.portrait{left:126px;top:97px;width:402px;height:402px;border-radius:50%;background:radial-gradient(circle at 50% 45%,#c9957a,#7a5a46 60%,#5b4d3d)}
.about .h2{left:582px;top:126px;position:absolute}
.about .bar{left:582px;top:178px;background:var(--orange)}
.about p{position:absolute;left:582px;top:208px;width:495px;font-size:15.5px;line-height:30px;color:var(--grey)}
.email{position:absolute;left:582px;top:400px;font-size:15.5px}
.email b{color:var(--orange);font-weight:500}
.btn-grad{position:absolute;background:linear-gradient(90deg,var(--gold),var(--orange));color:#fff;font-weight:500;font-size:15px;display:flex;align-items:center;justify-content:center;box-shadow:0 4px 8px rgba(0,0,0,.25)}
/* gallery */
.gallery{top:1408px;height:1000px;background:var(--grey-light)}
.tile{position:absolute;width:234px;box-shadow:0 3px 8px rgba(0,0,0,.15)}
.tile p{position:absolute;left:11px;top:12px;width:210px;color:#fff;font-weight:700;font-size:16px;line-height:30px}
/* packages */
.packages{top:2408px;height:290px;background:linear-gradient(90deg,#e4603d 0%,#e86a45 60%,#ec8a5e 100%)}
.packages .h2{position:absolute;left:111px;top:60px;color:#fff}
.packages .bar{left:111px;top:112px;background:#fff}
.packages p{position:absolute;left:111px;top:136px;width:740px;color:#fff;font-size:16px;line-height:30px}
/* explore */
.explore{top:2698px;height:806px}
.map{left:72px;top:216px;width:1027px;height:497px;background:radial-gradient(ellipse at 40% 50%,#5c6b74,#3f4a52 70%,#2f383f);border-radius:40% 45% 40% 45%/50% 40% 55% 45%}
.popup{left:612px;top:380px;width:276px;height:148px;background:#fff;border-radius:10px;box-shadow:0 6px 18px rgba(0,0,0,.25);padding:22px 26px}
.popup h3{font-size:20px;font-weight:500}
.popup p{font-size:10.5px;line-height:30px;color:var(--grey);margin-top:4px;line-height:29px}
/* testimonials */
.testimonials{top:3504px;height:616px;background:var(--grey-light)}
.card{position:absolute;top:209px;width:243px;height:243px;background:#fff;box-shadow:0 2px 8px rgba(0,0,0,.12);padding:16px 16px}
.card.fade{opacity:.35}
.card .who{display:flex;align-items:center;gap:14px}
.card .avatar{width:48px;height:48px;border-radius:50%;background:linear-gradient(135deg,#8a98a6,#5b6672)}
.card .who b{color:var(--orange);font-weight:500;font-size:16px}
.card p{font-size:12px;line-height:30px;color:#333;margin-top:8px}
.stars{color:var(--gold);font-size:14px;letter-spacing:2px;margin-top:4px}
.dots{left:573px;top:500px;display:flex;gap:4px}
.dots i{width:10px;height:10px;border-radius:50%;background:#444;display:block}
.dots i.on{background:var(--orange)}
/* news */
.news{top:4120px;height:765px}
.post{position:absolute;overflow:hidden}
.post .cap{position:absolute;left:30px;bottom:34px;right:30px;color:#fff}
.post .cap b{display:block;font-size:16px;font-weight:700;line-height:30px}
.post .cap span{display:block;font-size:12px;line-height:30px;opacity:.9}
/* footer */
.site-footer{top:4885px;height:406px;background:linear-gradient(90deg,#efa44a 0%,#e8784a 55%,#e4603d 100%);color:#fff}
.foot-brand{left:82px;top:96px;font-size:22px;font-weight:700}
.foot-brand small{display:block;font-size:9px;letter-spacing:3px;margin-top:4px;text-align:center}
.foot-about{left:82px;top:168px;width:280px;font-size:13px;line-height:30px}
.cards{left:90px;top:283px;display:flex;gap:6px}
.cards i{width:34px;height:22px;background:#fff;border-radius:2px;display:block;opacity:.9}
.foot-col h4{font-size:14px;font-weight:500;margin-bottom:10px}
.foot-col h4:after{content:"";display:block;width:40px;height:2px;background:#fff;margin-top:6px}
.foot-col li{list-style:none;font-size:13px;line-height:30px}
.foot-col li:before{content:"»";margin-right:16px}
.contact li{list-style:none;font-size:13px;line-height:30px;display:flex;gap:18px}
.contact svg{flex:none;margin-top:9px}
.foot-social{left:815px;top:240px;display:flex;gap:10px}
.foot-social i{width:13px;height:13px;border-radius:50%;background:#fff;display:block}
.foot-rule{left:0;top:343px;width:1200px;height:1px;background:rgba(255,255,255,.4)}
.copy{left:0;top:349px;width:1200px;text-align:center;font-size:12px}
</style>
</head>
<body>

<header class="site-header">
  <div class="abs search">
    <div class="btn"><svg width="14" height="14" viewBox="0 0 14 14"><circle cx="6" cy="6" r="4.5" fill="none" stroke="#fff" stroke-width="2"/><line x1="9.5" y1="9.5" x2="13" y2="13" stroke="#fff" stroke-width="2"/></svg></div>
    <span>Search Here</span>
  </div>
  <div class="abs brand">Harbors &amp; Hammocks<small>TRAVEL AGENCY</small></div>
  <div class="abs call">
    <div class="ico"><svg width="20" height="20" viewBox="0 0 24 24"><path d="M6.6 10.8a15 15 0 006.6 6.6l2.2-2.2c.3-.3.7-.4 1-.2 1.1.4 2.3.6 3.6.6.6 0 1 .4 1 1V20c0 .6-.4 1-1 1A17 17 0 013 4c0-.6.4-1 1-1h3.5c.6 0 1 .4 1 1 0 1.3.2 2.5.6 3.6.1.3 0 .7-.2 1z" fill="#fff"/></svg></div>
    <div><small>Call Us Today</small><strong>+1 555 014 2290</strong></div>
  </div>
  <div class="abs header-rule"></div>
  <nav class="abs nav">
    <a class="active" style="left:0">HOME</a>
    <a style="left:69px">ABOUT US</a>
    <a style="left:166px">DESTINATION</a>
    <a style="left:285px">PACKAGES</a>
    <a style="left:384px">CONSULTATION</a>
    <a style="left:511px">TESTIMONIALS</a>
    <a style="left:639px">CONTACT US</a>
  </nav>
  <div class="abs social"><i></i><i></i><i></i><i></i></div>
</header>

<section class="hero" role="img" aria-label="Globe with world landmarks, an airplane and clouds">
  <div class="abs welcome">WELCOME TO</div>
  <h1 class="abs hero-title">HARBORS AND HAMMOCKS TRAVEL AGENCY</h1>
  <p class="abs hero-sub">Lorem ipsum dolor sit amet, consectetur adipiscing elit, sed do eiusmod tempor incididunt ut labore et dolore magna aliqua.</p>
</section>

<form class="abs booking" style="position:absolute">
  <div class="field sep" style="left:35px"><b>CATEGORY</b><span>FLIGHTS</span><svg width="9" height="6"><path d="M1 1l3.5 3.5L8 1" stroke="#333" fill="none" stroke-width="1.5"/></svg></div>
  <div class="field sep" style="left:203px"><b>FROM</b><span>CHOOSE</span><svg width="9" height="6"><path d="M1 1l3.5 3.5L8 1" stroke="#333" fill="none" stroke-width="1.5"/></svg></div>
  <div class="field sep" style="left:349px"><b>TO</b><span>CHOOSE</span><svg width="9" height="6"><path d="M1 1l3.5 3.5L8 1" stroke="#333" fill="none" stroke-width="1.5"/></svg></div>
  <div class="field sep" style="left:506px"><b>DEPART</b><span>CHOOSE</span><svg width="9" height="6"><path d="M1 1l3.5 3.5L8 1" stroke="#333" fill="none" stroke-width="1.5"/></svg></div>
  <div class="field" style="left:662px"><b>RETURN</b><span>CHOOSE</span><svg width="9" height="6"><path d="M1 1l3.5 3.5L8 1" stroke="#333" fill="none" stroke-width="1.5"/></svg></div>
  <div class="book-now">BOOK NOW</div>
</form>

<section class="about">
  <div class="abs portrait" role="img" aria-label="Portrait of agency owner Marla Dunbevy"></div>
  <h2 class="h2">About <em>Marla Dunbevy</em></h2>
  <div class="bar"></div>
  <p>Marla has been traveling full time for the passed two years and has been very passionate about travel from a young age. Marla is dedicated to working closely with clients to book their dream vacation.Marla's specializations include honeymoons and anniversaries focusing on travel in Europe, Hawaii and all inclusive resorts in the Caribbean.</p>
  <div class="email"><b>EMAIL:</b>&nbsp; marla@harborsandhammockstravel.example</div>
  <div class="btn-grad" style="left:582px;top:452px;width:176px;height:45px">LEARN MORE</div>
</section>

<section class="gallery">
  <h2 class="h2 center" style="top:90px">World best travel <em>agency company</em></h2>
  <div class="bar" style="left:566px;top:142px"></div>
  <div class="tile" role="img" aria-label="Traveler in red dress above white village" style="left:111px;top:191px;height:327px;background:linear-gradient(180deg,#5d97d8,#cfd9e6 55%,#9a6c5a)"><p>Lorem ipsum dolor sit am etconsectetur</p></div>
  <div class="tile" role="img" aria-label="Hiker on a suspension bridge in forest" style="left:360px;top:191px;height:269px;background:linear-gradient(180deg,#6f7d58,#a29a80 55%,#4e5a3c)"><p>Lorem ipsum dolor sit am etconsectetur</p></div>
  <div class="tile" role="img" aria-label="Traveler sitting on coastal rocks" style="left:608px;top:191px;height:442px;background:linear-gradient(180deg,#c49a6a,#b0876a 50%,#6e5a4c)"><p>Lorem ipsum dolor sit am etconsectetur</p></div>
  <div class="tile" role="img" aria-label="Traveler in a boat on a turquoise lagoon" style="left:857px;top:191px;height:349px;background:linear-gradient(180deg,#7f8c8f,#3aa3a6 50%,#1c7c80)"><p>Lorem ipsum dolor sit am etconsectetur</p></div>
  <div class="tile" role="img" aria-label="Turtle swimming in deep sea water" style="left:111px;top:538px;height:349px;background:linear-gradient(180deg,#1e6c72,#165256 60%,#0f3b3e)"><p>Lorem ipsum dolor sit am etconsectetur</p></div>
  <div class="tile" role="img" aria-label="Smiling traveler in a sun hat" style="left:360px;top:478px;height:409px;background:linear-gradient(180deg,#5b7fa8,#c29a5a 50%,#7a5a30)"><p>Lorem ipsum dolor sit am etconsectetur</p></div>
  <div class="tile" role="img" aria-label="Couple at sunset by the sea" style="left:608px;top:653px;height:234px;background:linear-gradient(180deg,#233a5a,#c0703a 60%,#3a2a26)"><p>Lorem ipsum dolor sit am etconsectetur</p></div>
  <div class="tile" role="img" aria-label="Green mountain islands landscape" style="left:857px;top:559px;height:328px;background:linear-gradient(180deg,#8aa3c0,#8a7a4a 55%,#4a5a30)"><p>Lorem ipsum dolor sit am etconsectetur</p></div>
</section>

<section class="packages" aria-label="Vacation packages">
  <h2 class="h2">Our vacation packages</h2>
  <div class="bar"></div>
  <p>Lorem ipsum dolor sit amet, consectetur adipiscing elit, sed do eiusmod tempor incididunt ut labore et dolore magna aliqua. Quis ipsum suspendisse ultrices gravida. Risus commodo viverra maecenas accumsan lacus vel facilisis.</p>
  <div class="btn-grad" style="left:890px;top:122px;width:179px;height:49px">DETAILS</div>
</section>

<section class="explore">
  <h2 class="h2 center" style="top:90px">Explore the <em>world for travel</em></h2>
  <div class="bar" style="left:566px;top:142px"></div>
  <div class="abs map" role="img" aria-label="World map with city imagery and destination markers"></div>
  <svg class="abs" style="left:320px;top:2800px;position:absolute" width="0" height="0"></svg>
  <svg class="abs" style="left:316px;top:406px" width="70" height="96" viewBox="0 0 70 96"><path d="M35 94C15 62 2 48 2 33a33 33 0 0166 0c0 15-13 29-33 61z" fill="#f0a040" stroke="#e4603d" stroke-width="3"/><text x="35" y="40" text-anchor="middle" font-family="Roboto,sans-serif" font-size="18" fill="#fff">3</text></svg>
  <svg class="abs" style="left:421px;top:366px" width="70" height="96" viewBox="0 0 70 96"><path d="M35 94C15 62 2 48 2 33a33 33 0 0166 0c0 15-13 29-33 61z" fill="#f0a040" stroke="#e4603d" stroke-width="3"/><text x="35" y="40" text-anchor="middle" font-family="Roboto,sans-serif" font-size="18" fill="#fff">1</text></svg>
  <svg class="abs" style="left:600px;top:282px" width="70" height="96" viewBox="0 0 70 96"><path d="M35 94C15 62 2 48 2 33a33 33 0 0166 0c0 15-13 29-33 61z" fill="#f0a040" stroke="#e4603d" stroke-width="3"/><text x="35" y="40" text-anchor="middle" font-family="Roboto,sans-serif" font-size="18" fill="#fff">2</text></svg>
  <div class="abs popup"><h3>EUROPE</h3><p>Lorem ipsum dolor sit amet, consectetur adipiscing elit, sed do eiusmod tempor incididunt ut labore et dolore magna aliqua. Quis</p></div>
</section>

<section class="testimonials">
  <h2 class="h2 center" style="top:95px">What our <em>happy customers says</em></h2>
  <div class="bar" style="left:566px;top:147px"></div>
  <div class="card fade" style="left:-45px"><div class="who"><div class="avatar"></div><b>John Deo</b></div><p>Lorem ipsum dolor sit amet, conse ctetur adipiscing elit, sed do eius mod tempor incididunt ut labore et dolore magna aliqua.</p><div class="stars">★★★★★</div></div>
  <div class="card" style="left:216px"><div class="who"><div class="avatar"></div><b>John Deo</b></div><p>Lorem ipsum dolor sit amet, conse ctetur adipiscing elit, sed do eius mod tempor incididunt ut labore et dolore magna aliqua.</p><div class="stars">★★★★★</div></div>
  <div class="card" style="left:478px"><div class="who"><div class="avatar"></div><b>John Deo</b></div><p>Lorem ipsum dolor sit amet, conse ctetur adipiscing elit, sed do eius mod tempor incididunt ut labore et dolore magna aliqua.</p><div class="stars">★★★★★</div></div>
  <div class="card" style="left:740px"><div class="who"><div class="avatar"></div><b>John Deo</b></div><p>Lorem ipsum dolor sit amet, conse ctetur adipiscing elit, sed do eius mod tempor incididunt ut labore et dolore magna aliqua.</p><div class="stars">★★★★★</div></div>
  <div class="card fade" style="left:1001px"><div class="who"><div class="avatar"></div><b>John Deo</b></div><p>Lorem ipsum dolor sit amet, conse ctetur adipiscing elit, sed do eius mod tempor incididunt ut labore et dolore magna aliqua.</p><div class="stars">★★★★★</div></div>
  <div class="abs dots"><i></i><i class="on"></i><i></i><i></i></div>
</section>

<section class="news">
  <h2 class="h2 center" style="top:90px">Stay update <em>with Harbors</em></h2>
  <div class="bar" style="left:566px;top:142px"></div>
  <article class="post" role="img" aria-label="Friends laughing together at a table" style="left:144px;top:197px;width:450px;height:473px;background:linear-gradient(180deg,#6a6a6a,#3e3a38 60%,#1f1d1c)">
    <div class="cap"><b>Lorem ipsum dolor sit amet, consectetur adi piscing elit, sed do eiusmod tempor</b><span>Lorem ipsum dolor sit amet, consectetur adipiscing elit, sed do eiusmod tempor</span></div>
  </article>
  <article class="post" role="img" aria-label="Couple smiling outdoors" style="left:606px;top:197px;width:450px;height:229px;background:linear-gradient(180deg,#7a7a7a,#4a4644 70%,#2a2826)">
    <div class="cap" style="bottom:40px"><b>Lorem ipsum dolor sit amet, consectetur adi piscing elit, sed do eiusmod tempor</b><span>Lorem ipsum dolor sit amet, consectetur adipiscing elit, sed do eiusmod tempor</span></div>
  </article>
  <article class="post" role="img" aria-label="Friends chatting in a bright room" style="left:606px;top:438px;width:450px;height:232px;background:linear-gradient(180deg,#8a8a8a,#4c4846 70%,#2a2826)">
    <div class="cap" style="bottom:40px"><b>Lorem ipsum dolor sit amet, consectetur adi piscing elit, sed do eiusmod tempor</b><span>Lorem ipsum dolor sit amet, consectetur adipiscing elit, sed do eiusmod tempor</span></div>
  </article>
</section>

<footer class="site-footer">
  <div class="abs foot-brand">Harbors &amp; Hammocks<small>TRAVEL AGENCY</small></div>
  <p class="abs foot-about">Lorem ipsum dolor sit amet, consec tetur adipiscing elit, sed do eiusmod tempor incididunt ut labore et aliqua.</p>
  <div class="abs cards"><i></i><i></i><i></i><i></i></div>
  <div class="abs foot-col" style="left:405px;top:68px"><h4>QUICK LINKS</h4><ul><li>Home</li><li>Destination</li><li>Packages</li><li>Consultation</li><li>Testimonials</li></ul></div>
  <div class="abs foot-col" style="left:594px;top:68px"><h4>IMPORTANT</h4><ul><li>Privacy Policy</li><li>Refund Policy</li><li>Terms &amp; Conditions</li><li>About Us</li><li>Contact Us</li></ul></div>
  <div class="abs foot-col" style="left:808px;top:68px"><h4>CONTACT INFO</h4>
    <ul class="contact">
      <li><svg width="12" height="16" viewBox="0 0 12 16"><path d="M6 16C2 10 0 7.5 0 6a6 6 0 0112 0c0 1.5-2 4-6 10z" fill="#fff"/><circle cx="6" cy="6" r="2" fill="#e87a48"/></svg><span>123 Lorem ipsum dolor sit amet,<br>consectetur adipiscing</span></li>
      <li><svg width="14" height="14" viewBox="0 0 24 24"><path d="M6.6 10.8a15 15 0 006.6 6.6l2.2-2.2c.3-.3.7-.4 1-.2 1.1.4 2.3.6 3.6.6.6 0 1 .4 1 1V20c0 .6-.4 1-1 1A17 17 0 013 4c0-.6.4-1 1-1h3.5c.6 0 1 .4 1 1 0 1.3.2 2.5.6 3.6.1.3 0 .7-.2 1z" fill="#fff"/></svg><span>+1 555 014 2290</span></li>
      <li><svg width="14" height="11" viewBox="0 0 14 11"><rect width="14" height="11" rx="1" fill="#fff"/><path d="M1 1l6 5 6-5" stroke="#e87a48" fill="none" stroke-width="1.4"/></svg><span>marla@harborsandhammockstravel.example</span></li>
    </ul>
  </div>
  <div class="abs foot-social"><i></i><i></i><i></i><i></i></div>
  <div class="abs foot-rule"></div>
  <p class="abs copy">© Copyrights 2021 Harbors and Hammocks Travel &nbsp;|&nbsp; &nbsp;All Rights Reserved</p>
</footer>

</body>
</html>
```